Oil and Gas Exploration and Production company needs a business card design

We need a business card design using our logo and colors in the logo. We want a mainstream design.

```html
<!DOCTYPE html>
<html lang="en">
<head>
<meta charset="utf-8">
<title>Andara Oil &amp; Gas – Business Card</title>
<link rel="stylesheet" href="https://fonts.googleapis.com/css2?family=EB+Garamond:wght@400;600;700&display=swap">
<style>
  :root {
    --page-bg: #e9e9e9;
    --card-bg: #f7f7f7;
    --gold: #c99a2e;
    --ink: #1a1a1a;
  }
  html, body {
    margin: 0;
    padding: 0;
    width: 1200px;
    height: 586px;
    overflow: hidden;
    background: var(--page-bg);
  }
  .card {
    position: absolute;
    left: 130px;
    top: 11px;
    width: 940px;
    height: 564px;
    background: var(--card-bg);
    font-family: "EB Garamond", Garamond, serif;
    color: var(--ink);
  }
  .brand {
    position: absolute;
    left: 0;
    right: 0;
    top: 92px;
    display: flex;
    justify-content: center;
    align-items: center;
    gap: 16px;
  }
  .brand-mark {
    width: 44px;
    height: 44px;
    border-radius: 50%;
    background: var(--gold);
  }
  .brand-name {
    font-size: 56px;
    font-weight: 700;
    color: var(--ink);
    line-height: 1;
    letter-spacing: 0.5px;
  }
  .holder {
    position: absolute;
    right: 70px;
    top: 333px;
    text-align: right;
  }
  .holder-name {
    font-size: 22px;
    font-weight: 700;
    color: var(--gold);
    line-height: 1.2;
  }
  .holder-role {
    font-size: 18px;
    line-height: 1.25;
    margin-top: 2px;
  }
  .rule {
    position: absolute;
    left: 52px;
    top: 383px;
    width: 646px;
    height: 4px;
    background: var(--gold);
  }
  .contacts {
    position: absolute;
    left: 52px;
    top: 404px;
    margin: 0;
    padding: 0;
    list-style: none;
    font-size: 19px;
  }
  .contacts li {
    display: flex;
    align-items: center;
    height: 38.5px;
  }
  .contacts svg,
  .contacts .social-dot {
    width: 20px;
    height: 18px;
    margin-right: 18px;
    flex: none;
  }
  .social-dot {
    display: inline-block;
    width: 16px !important;
    height: 16px !important;
    border-radius: 50%;
    background: var(--gold);
    margin-left: 2px;
  }
  .address {
    position: absolute;
    right: 70px;
    top: 451px;
    text-align: right;
    font-size: 20px;
    font-weight: 700;
    color: var(--gold);
    line-height: 29px;
    font-style: normal;
  }
  .footer-band {
    position: absolute;
    left: 0;
    bottom: 0;
    width: 100%;
    height: 15px;
    background: var(--gold);
  }
</style>
</head>
<body>
  <div class="card">
    <div class="brand">
      <span class="brand-mark"></span>
      <span class="brand-name">Andara Oil &amp; Gas</span>
    </div>

    <div class="holder">
      <div class="holder-name">Marina Velasco</div>
      <div class="holder-role">Chief Executive Offer</div>
    </div>

    <div class="rule"></div>

    <ul class="contacts">
      <li>
        <svg viewBox="0 0 20 18" aria-hidden="true">
          <path fill="var(--gold)" d="M1 6c0-3 4-5 9-5s9 2 9 5l-4 1-1-2c-2-1-6-1-8 0L5 7 1 6zM5 8h10l3 8H2l3-8zm5 2a2.5 2.5 0 1 0 0 5 2.5 2.5 0 0 0 0-5z"/>
        </svg>
        <span>+34 900 123 456.</span>
      </li>
      <li>
        <svg viewBox="0 0 20 18" aria-hidden="true">
          <rect x="1" y="3" width="18" height="13" fill="var(--gold)"/>
          <path d="M1.5 3.5 10 10l8.5-6.5" fill="none" stroke="var(--card-bg)" stroke-width="1.6"/>
        </svg>
        <span>info@andaraoil&amp;gas</span>
      </li>
      <li>
        <span class="social-dot"></span>
        <span>@andaraoil&amp;gas</span>
      </li>
    </ul>

    <address class="address">
      Calle del Olmo 14<br>
      Oficina 2B, 24002, León
    </address>

    <div class="footer-band"></div>
  </div>
</body>
</html>
```